Cat-products company needs smart, yet endearing, business card

We need a business card design for a new, but up-and-running, business based in Honolulu, Hawaii. The business is Purrnest Nook Co. Our first product is the most environmentally-friendly cat grass kit ever seen on the planet. Future products, currently in the R&D phase, will include a variety of exciting cat scratchers. We also do consulting work to help apartment-dwellers make their home more cat-friendly and, in the future, plan on doing full, custom installs of structure to create high walkways for cats.

Target Market(s)

Middle-aged, apartment-dwelling, middle-class workers who own 1 or more cats and who dote on them.

Industry/Entity Type

Pet Care

Contact Information for Business Card

A striking, professional, yet warm and friendly design is what we're after.

Font styles to use
Serif
Sans Serif
Other font styles liked:
• Comfortaa

Colors

Designer to choose colors to be used in the design.

Requirements
Must have
• The company logo: (see attachment)
• The company name: Purrnest Nook Co
• The web address: www.purrnestnookco.com
• Email: support@purrnestnookco.com
• Phone: +1 (808) 571 6023
• Update (Fri Jun 30 3017 7:45pm Hawaii Time) I would like, is possible, uploaded picture of the cat grass kit on the back of the card with some text along the lines of: Purrnest Nook Co - Maker Of The Leafiest Feline Sprout Set Yet
Nice to have
• A cat picture, cartoon, real or silhouette that illustrates cats in action and/or relaxing; ie using the apartment space to live, play and relax in and being well-contented.
• Most of the website is done in the font: Comfortaa. It might be nice to continue using this for brand consistency.
Should not have
• Hard-to-read fonts.

```html
<!DOCTYPE html>
<html lang="en">
<head>
<meta charset="utf-8">
<title>Purrnest Nook Co — Business Card</title>
<link href="https://fonts.googleapis.com/css2?family=Source+Sans+3:wght@400;600;700&display=swap" rel="stylesheet">
<style>
  :root {
    --stage: #131313;
    --card-front: #ffffff;
    --card-back: #5a3630;
    --amber: #fdb304;
    --ink: #1c1c1c;
    --rule: #4a4a4a;
  }
  html, body {
    margin: 0;
    width: 1200px;
    height: 900px;
    overflow: hidden;
    background: var(--stage);
    font-family: "Source Sans 3", "Myriad Pro", sans-serif;
  }
  .stage { position: relative; width: 1200px; height: 900px; }
  .card {
    position: absolute;
    top: 306px;
    width: 440px;
    height: 271px;
    border-radius: 12px;
  }
  .card--front { left: 149px; background: var(--card-front); }
  .card--back { left: 608px; background: var(--card-back); display: flex; align-items: center; justify-content: center; }

  .brand {
    position: absolute;
    left: 30px;
    width: 170px;
    top: 90px;
    text-align: center;
    color: var(--amber);
    font-weight: 700;
    font-size: 30px;
    line-height: 1.05;
    letter-spacing: 0.3px;
  }
  .divider {
    position: absolute;
    left: 210px;
    top: 73px;
    width: 1px;
    height: 123px;
    background: var(--rule);
  }
  .holder { position: absolute; left: 237px; top: 69px; }
  .holder__name {
    margin: 0;
    color: var(--amber);
    font-size: 16.5px;
    font-weight: 600;
    letter-spacing: 0.2px;
    line-height: 1.1;
  }
  .holder__title { margin: 2px 0 0; color: var(--ink); font-size: 12.5px; }

  .contacts {
    position: absolute;
    left: 237px;
    top: 152px;
    margin: 0;
    padding: 0;
    list-style: none;
    color: var(--ink);
    font-size: 12.5px;
    line-height: 16px;
  }
  .contacts li { display: flex; align-items: center; gap: 5px; }
  .contacts svg { width: 10px; height: 10px; fill: var(--amber); flex: none; }

  .back-name {
    color: var(--amber);
    font-weight: 700;
    font-size: 34px;
    letter-spacing: 0.4px;
  }
</style>
</head>
<body>
<main class="stage">
  <section class="card card--front" aria-label="Business card front">
    <div class="brand">Purrnest<br>Nook Co</div>
    <div class="divider"></div>
    <div class="holder">
      <p class="holder__name">MARCUS ELLERY</p>
      <p class="holder__title">Managing Director</p>
    </div>
    <ul class="contacts">
      <li>
        <svg viewBox="0 0 10 10" aria-hidden="true"><path d="M2 0.5l2 2-1 1.3c.6 1.3 1.6 2.3 2.9 2.9l1.3-1 2 2-1.3 1.6C4.7 9.3.7 5.3.4 1.8z"/></svg>
        +1 (808) 571 6023
      </li>
      <li>
        <svg viewBox="0 0 10 10" aria-hidden="true"><path d="M0 2h10v6H0z M0 2l5 3.3L10 2" stroke="#fff" stroke-width="0.8"/></svg>
        support@purrnestnookco.com
      </li>
      <li>
        <svg viewBox="0 0 10 10" aria-hidden="true"><circle cx="5" cy="5" r="4.6"/><path d="M5 .5v9M.5 5h9" stroke="#fff" stroke-width="0.7"/></svg>
        www.purrnestnookco.com
      </li>
    </ul>
  </section>

  <section class="card card--back" aria-label="Business card back">
    <span class="back-name">Purrnest Nook Co</span>
  </section>
</main>
</body>
</html>
```